Agriculture Security Company needs a business card design

We need a business card design for a new company based in Seattle calls Ferncrest Guardline LLC. We provide high-end physical security solutions that is geared and focused towards to the marijuana grow operations, wholesalers and distributors. We DO NOT get involved in the retail operations (store fronts). We would like to see designs that incorporate professionalism, reliability, trustworthy and forward thinking as traits of our organization.

Industry/Entity Type

Security

```html
<!DOCTYPE html>
<html lang="en">
<head>
<meta charset="utf-8">
<title>Ferncrest Guardline business card</title>
<link rel="stylesheet" href="https://fonts.googleapis.com/css2?family=Ubuntu:wght@400;500;700&display=swap">
<style>
  :root {
    --bg: #e9e6e0;
    --paper: #f6f6f4;
    --green: #1f7a3c;
    --green-dark: #17662f;
    --green-light: #8cbf4f;
    --sky: #4f97d3;
    --ink-light: #ffffff;
    --ink-soft: rgba(255,255,255,0.85);
  }
  * { margin: 0; padding: 0; box-sizing: border-box; }
  html, body { width: 1200px; height: 1023px; overflow: hidden; }
  body {
    background: var(--bg);
    font-family: "Ubuntu", sans-serif;
    position: relative;
  }
  .card {
    position: absolute;
    width: 600px;
    height: 343px;
    left: 300px;
    border-radius: 4px;
    overflow: hidden;
    box-shadow: 0 12px 30px rgba(0,0,0,0.25);
  }
  .card-front { top: 118px; background: var(--paper); }
  .card-back { top: 562px; background: var(--green); }
  .card svg.waves { position: absolute; inset: 0; }

  .holder { position: absolute; top: 36px; left: 150px; width: 170px; text-align: right; }
  .holder-name { color: var(--green); font-weight: 700; font-size: 22px; white-space: nowrap; }
  .holder-role { color: var(--green-light); font-size: 12px; margin-top: 4px; }

  .brand-name {
    position: absolute;
    color: var(--green);
    font-weight: 700;
    letter-spacing: 1px;
  }
  .card-front .brand-name { left: 44px; top: 196px; font-size: 38px; }

  .contact {
    position: absolute;
    right: 36px;
    top: 48px;
    text-align: right;
    color: var(--ink-soft);
    font-size: 12.5px;
    line-height: 1.55;
  }
  .contact .company { color: var(--ink-light); font-weight: 700; }
  .contact .block { margin-bottom: 22px; }
  .contact .row { display: flex; justify-content: flex-end; align-items: center; gap: 8px; }
  .contact .row svg { width: 11px; height: 11px; fill: var(--ink-soft); }

  .card-back .brand-name {
    left: 0; right: 0; top: 142px;
    text-align: center;
    color: var(--ink-light);
    font-size: 44px;
  }
  .back-web {
    position: absolute;
    left: 32px;
    top: 50%;
    transform: translate(-50%, -50%) rotate(-90deg);
    color: var(--ink-soft);
    font-size: 12px;
    letter-spacing: 3px;
    white-space: nowrap;
  }
</style>
</head>
<body>

<section class="card card-front" aria-label="Business card front">
  <svg class="waves" viewBox="0 0 600 343" width="600" height="343" aria-hidden="true">
    <path d="M405 0 C 365 80, 355 150, 335 200 C 315 260, 265 300, 225 343 L 600 343 L 600 0 Z" fill="var(--green)"/>
    <path d="M390 0 C 365 40, 352 90, 340 140" stroke="var(--sky)" stroke-width="11" fill="none" stroke-linecap="round"/>
    <path d="M316 185 C 304 258, 255 300, 205 343" stroke="var(--green-light)" stroke-width="10" fill="none"/>
    <path d="M600 300 C 520 320, 440 330, 300 343 L 600 343 Z" fill="var(--green-dark)" opacity="0.5"/>
  </svg>

  <div class="holder">
    <div class="holder-name">Dana Whitlow</div>
    <div class="holder-role">President</div>
  </div>

  <div class="brand-name">Ferncrest</div>

  <div class="contact">
    <div class="block">
      <div class="company">Ferncrest Guardline LLC</div>
      <div>2150 Alder Crest Way</div>
      <div>Renton, WA 98055</div>
    </div>
    <div class="row">206-555-0148
      <svg viewBox="0 0 16 16"><path d="M3 1l3 3-1.5 2c1 2 3 4 5 5l2-1.5 3 3-2 2C6 14 2 10 1 3z"/></svg>
    </div>
    <div class="row">info@ferncrestguardline.com
      <svg viewBox="0 0 16 16"><path d="M1 3h14v10H1z"/></svg>
    </div>
    <div class="row">www.ferncrestguardline.com
      <svg viewBox="0 0 16 16"><circle cx="8" cy="8" r="7"/></svg>
    </div>
  </div>
</section>

<section class="card card-back" aria-label="Business card back">
  <svg class="waves" viewBox="0 0 600 343" width="600" height="343" aria-hidden="true">
    <path d="M80 343 C 60 200, 250 60, 600 90" stroke="rgba(255,255,255,0.12)" stroke-width="10" fill="none"/>
    <path d="M140 343 C 150 250, 330 170, 600 200" stroke="rgba(255,255,255,0.10)" stroke-width="6" fill="none"/>
    <path d="M0 300 C 200 270, 420 300, 600 260 L 600 343 L 0 343 Z" fill="rgba(0,0,0,0.08)"/>
  </svg>
  <div class="brand-name">Ferncrest</div>
  <div class="back-web">www.ferncrestguardline.com</div>
</section>

</body>
</html>
```